Maple Gable Business Card

Colors can be blue, grey and white as you see in the attached logo. Needs to have a spot for name, title, phone, email, address, and website. There also needs to be a spot for an agent's picture.

Contact Information for Business Card

See project description.

Colors

Designer to choose colors to be used in the design.

```html
<!DOCTYPE html>
<html lang="en">
<head>
<meta charset="utf-8">
<title>Maple Gable Business Card</title>
<link rel="stylesheet" href="https://fonts.googleapis.com/css2?family=Montserrat:wght@400;500;600&display=swap">
<style>
  :root {
    --backdrop: #4a4548;
    --card: #1c1c1e;
    --card-edge: #252527;
    --blue: #3d7cc9;
    --white: #f2f2f2;
    --photo-top: #4b5560;
    --photo-bottom: #2c3138;
  }
  * { box-sizing: border-box; margin: 0; padding: 0; }
  html, body { width: 1200px; height: 912px; overflow: hidden; }
  body {
    background: var(--backdrop);
    font-family: "Montserrat", sans-serif;
    position: relative;
  }
  .card {
    position: absolute;
    width: 700px;
    height: 400px;
    background: linear-gradient(160deg, var(--card-edge), var(--card) 60%);
    box-shadow: 0 12px 30px rgba(0,0,0,.45);
  }
  .card--front { left: 90px; top: 40px; }
  .card--back { left: 410px; top: 472px; }

  /* Brand name */
  .brand { display: flex; align-items: center; gap: 14px; }
  .brand__square { width: 20px; height: 20px; background: var(--blue); flex: none; }
  .brand__name {
    color: var(--blue); font-weight: 600; letter-spacing: 1px; line-height: 1; white-space: nowrap;
  }
  .card--front .brand {
    position: absolute; left: 50%; top: 50%; transform: translate(-50%, -50%);
  }
  .card--front .brand__name { font-size: 44px; }
  .card--back .brand { position: absolute; left: 48px; top: 56px; }
  .card--back .brand__name { font-size: 34px; }

  /* Agent photo spot */
  .agent-photo {
    position: absolute; left: 48px; top: 176px; width: 100px; height: 128px;
    background: linear-gradient(180deg, var(--photo-top), var(--photo-bottom));
  }

  /* Contact block */
  .agent { position: absolute; left: 172px; top: 176px; }
  .agent__name { font-size: 28px; font-weight: 500; letter-spacing: 1px; color: var(--white); line-height: 1.1; }
  .agent__first { color: var(--blue); }
  .agent__title { font-size: 18px; color: var(--white); margin-top: 4px; }
  .contact { list-style: none; margin-top: 16px; font-size: 18px; color: var(--white); line-height: 1.4; }
  .contact__label { color: var(--blue); }
  .contact__site strong { font-weight: 600; }
  .rule {
    position: absolute; left: 172px; right: 40px; top: 330px; height: 1px; background: var(--blue);
  }
  .address { position: absolute; left: 172px; top: 344px; font-size: 18px; color: var(--white); }
</style>
</head>
<body>
  <section class="card card--front" aria-label="Card front">
    <div class="brand">
      <span class="brand__square"></span>
      <span class="brand__name">MAPLE GABLE</span>
    </div>
  </section>

  <section class="card card--back" aria-label="Card back">
    <div class="brand">
      <span class="brand__name">MAPLE GABLE</span>
    </div>
    <div class="agent-photo" role="img" aria-label="Agent portrait photo"></div>
    <div class="agent">
      <p class="agent__name"><span class="agent__first">DANIEL</span> HARTLEY</p>
      <p class="agent__title">Director</p>
      <ul class="contact">
        <li><span class="contact__label">P:</span> (555) 284-6130</li>
        <li><span class="contact__label">E:</span> info@maplegable.com | <span class="contact__label">W:</span> <span class="contact__site">www.<strong>maplegable</strong>.com</span></li>
      </ul>
    </div>
    <div class="rule"></div>
    <p class="address">812 Willow Crest Lane Reno, NV 89501</p>
  </section>
</body>
</html>
```